Migration and redesign of existing website to WordPress using DIVI 3

I. TASK OBJECTIVE:
- Redesign our existing website www.kelvaleheelcare.com.au with a fresh new look and migrate to new Wordpress site based on DIVI3 theme. The site will contain the same basic functionality as the existing site (with some small changes).

II. STYLE/ DESIGN ASPECT:
As an example of a site that I like the look of, see https://pebblequarn.com/. I like the use of shadows, and this would go well with the little animations you can do with Divi (e.g. when hovering over pics).

1. What I am looking for is a design which has lots of white space, is modern and friendly looking (but still not too cute or frivolous, as we are a medical practice)
2. DESIGN that is NOT TOO rectangular or blocky.
3. Please take into consideration our Users are Older market, so any icons or navigation features need to be very easy to understand and not too small.
4. Must be easy to navigate
5. We are are happy to go with a new colour scheme, and are working on some ideas for this, but happy to take suggestions.

III. SPECIFICATIONS:
1. 5+ Pages (should flow like the current site)
2. Using Wordpress Divi 3 theme.
3. I'd like every page to have a "book now" button and a contact form in a sidebar so that users can click the button or fill in the contact form without scrolling at all. EXCEPT ON THE HOME PAGE, where there should still be a book now button (maybe on the top right in the header of all pages?), and maybe a contact us button which scrolls down to the contact area at the bottom of the HOME page. I don't think a side bar is necessarily required on the home page, but if you think it makes sense from a design perspective please let me know.
4. AT THE BOTTOM OF THE PAGE, just above the FOOTER, I'd like a row of trust logos for various organisations that we are affiliated with. (A list of this company will be provided later but you could temporarily use placeholders)

Once we have a structure in place, we can migrate most of the content. Please let me know if I'm not being clear or you need further information.

Podiatry Customers and Referrors

Health Care

5+ page

• Simple to navigate.
• Contact/booking details on most if not all pages - please see specification above
• Section for Trusted Affiliates above the footer
• Wordpress using Divi3 Theme
• Not too busy with the design. Plenty of white space or light background.
• Should not be complicated to navigate.
• TOO rectangular or blocky designs

```html
<!DOCTYPE html>
<html lang="en">
<head>
<meta charset="utf-8">
<title>Kelvale Heel Care – Podiatry</title>
<link href="https://fonts.googleapis.com/css2?family=Open+Sans:wght@400;600;700;800&display=swap" rel="stylesheet">
<style>
:root{
  --teal:#1a7d80;
  --teal-dark:#11676a;
  --green:#4d8a4f;
  --ink:#333;
  --muted:#666;
  --line:#d9d9d9;
  --grey-bg:#eeeff1;
  --badge:#d5d9dc;
  --white:#fff;
  --radius:8px;
  --shadow:0 6px 16px rgba(0,0,0,.14);
}
*{box-sizing:border-box;margin:0;padding:0}
html,body{width:1200px;height:3673px;overflow:hidden}
body{position:relative;font-family:"Open Sans",Arial,sans-serif;color:var(--ink);background:var(--white)}
.abs{position:absolute}
.btn{position:absolute;display:flex;align-items:center;justify-content:center;background:var(--green);color:var(--white);font-weight:700;text-transform:uppercase;letter-spacing:.5px;text-decoration:none;border-radius:4px;box-shadow:0 3px 8px rgba(0,0,0,.15)}
.section-title{position:absolute;left:0;width:1200px;text-align:center;color:var(--teal);font-weight:700;font-size:21px;text-transform:uppercase}
.section-title::after{content:"";display:block;width:52px;height:3px;border-radius:2px;background:var(--teal);margin:14px auto 0}

/* header */
.site-header{position:absolute;left:0;top:0;width:1200px;height:113px;background:var(--white);box-shadow:0 2px 8px rgba(0,0,0,.08);z-index:2}
.brand{position:absolute;left:135px;top:22px;display:flex;align-items:center;gap:12px;color:var(--teal);font-weight:700;font-size:22px}
.brand-dot{width:40px;height:40px;border-radius:50%;background:var(--teal)}
.call{position:absolute;left:645px;top:22px;display:flex;align-items:center;gap:10px}
.call-icon{width:34px;height:34px;border-radius:50%;background:var(--teal);display:flex;align-items:center;justify-content:center}
.call small{display:block;font-size:10px;font-weight:600;color:var(--muted)}
.call strong{display:block;font-size:21px;color:var(--teal);line-height:1}
.search{position:absolute;left:845px;top:26px;width:120px;height:32px;border:1px solid var(--line);border-radius:16px;font-size:10px;color:#999;display:flex;align-items:center;gap:6px;padding-left:12px}
.header-book{left:975px;top:26px;width:92px;height:32px;font-size:11px}
.main-nav{position:absolute;left:384px;top:78px;display:flex;font-size:11.5px;font-weight:600;text-transform:uppercase}
.main-nav a{padding:5px 10px;color:var(--ink);text-decoration:none;border-radius:3px}
.main-nav a.active{background:var(--teal);color:var(--white)}

/* hero */
.hero-photo{position:absolute;left:0;top:113px;width:1200px;height:560px;background:linear-gradient(120deg,#e6c4ad 0%,#d9a98c 30%,#c89a72 55%,#e2cdb2 100%)}
.hero-tag{position:absolute;left:676px;top:306px;width:475px;height:98px;background:rgba(42,140,150,.92);border-radius:var(--radius);box-shadow:var(--shadow);color:var(--white);font-weight:800;font-size:28px;line-height:38px;padding:10px 0 0 28px;text-transform:uppercase}
.hero-dots{position:absolute;left:552px;top:622px;display:flex;gap:8px}
.hero-dots i{width:9px;height:9px;border-radius:50%;background:rgba(255,255,255,.75)}

/* practice areas */
.area{position:absolute;top:803px;width:245px}
.area-photo{width:245px;height:240px;border-radius:var(--radius);box-shadow:var(--shadow)}
.area h3{margin-top:18px;font-size:12.5px;font-weight:600;text-transform:uppercase;padding-bottom:8px;border-bottom:1px solid var(--line)}
.area ul{list-style:none;margin-top:14px;font-size:11px;line-height:17px;color:var(--muted)}
.area li{padding-left:14px;position:relative}
.area li::before{content:"";position:absolute;left:2px;top:6px;border-left:5px solid var(--teal);border-top:3px solid transparent;border-bottom:3px solid transparent}
.area .btn{position:relative;margin-top:18px;width:72px;height:22px;font-size:9px}

/* banner */
.banner{position:absolute;left:0;top:1259px;width:1200px;height:494px;background:linear-gradient(90deg,#3c7f96 0%,#5b93a5 45%,#a9b07a 70%,#7e9a68 100%)}
.banner h2{position:absolute;left:150px;top:110px;width:500px;color:var(--white);font-weight:800;font-size:23px;line-height:31px;text-transform:uppercase}
.banner p{position:absolute;left:150px;top:218px;width:440px;color:rgba(255,255,255,.9);font-size:11.5px;line-height:20px}
.banner .btn{left:150px;top:330px;width:122px;height:38px;font-size:12px}

/* team */
.team{position:absolute;left:0;top:1753px;width:1200px;height:434px;background:var(--grey-bg)}
.member{position:absolute;top:151px;width:160px;text-align:center}
.avatar{width:160px;height:160px;border-radius:50%;background:linear-gradient(160deg,#f2f2f2,#d8d4cf);border:5px solid var(--white);box-shadow:0 4px 10px rgba(0,0,0,.12)}
.member strong{display:block;margin-top:24px;font-size:13px;font-weight:600}
.member span{display:block;font-size:11px;color:var(--muted)}
.arrow{position:absolute;top:214px;width:34px;height:34px;border-radius:50%;background:var(--green);display:flex;align-items:center;justify-content:center;z-index:1;box-shadow:0 2px 6px rgba(0,0,0,.2)}

/* cases */
.case{position:absolute;top:2331px;height:285px;display:flex;flex-direction:column;align-items:center;justify-content:center;color:var(--white);border-radius:var(--radius);box-shadow:var(--shadow)}
.case h3{font-size:18px;font-weight:800;text-transform:uppercase}
.case span{margin-top:14px;border:2px solid var(--white);border-radius:4px;padding:6px 20px;font-size:11px;font-weight:700;text-transform:uppercase}

/* book */
.book-band{position:absolute;left:0;top:2785px;width:1200px;height:426px;background:linear-gradient(90deg,#1d7f82 0%,#2a8b86 60%,#3f918a 100%)}
.book{position:absolute;left:225px;top:2768px;width:288px;height:460px;background:var(--white);border-radius:4px;box-shadow:8px 10px 20px rgba(0,0,0,.35);overflow:hidden}
.book-top{height:130px;background:#1f6e9a;color:var(--white);padding:14px 16px}
.book-top h4{font-size:27px;font-weight:700}
.book-top p{font-size:10px;margin-top:4px}
.book-meta{padding:10px 16px;font-size:9px;color:var(--muted);line-height:13px}
.book-photo{position:absolute;left:0;bottom:0;width:288px;height:245px;background:linear-gradient(160deg,#8fb6c6,#3d6f86)}
.book-copy{position:absolute;left:598px;top:2888px;width:460px;color:var(--white)}
.book-copy h2{font-size:23px;font-weight:400;line-height:32px}
.book-copy p{margin-top:22px;font-size:11.5px;line-height:19px;opacity:.9}
.book-copy .btn{position:relative;margin-top:28px;width:128px;height:38px;font-size:12px}

/* affiliates */
.affiliates{position:absolute;left:0;top:3211px;width:1200px;height:100px;background:var(--white);display:flex;align-items:center;justify-content:center;gap:44px}
.affiliates i{width:120px;height:46px;border-radius:10px;background:var(--badge)}

/* footer */
.site-footer{position:absolute;left:0;top:3311px;width:1200px;height:362px;background:var(--grey-bg)}
.site-footer h4{font-size:12px;font-weight:700;text-transform:uppercase}
.field{position:absolute;height:34px;background:var(--white);border:1px solid var(--line);border-radius:4px;font-size:10px;color:#888;padding:10px}
.foot-menu{position:absolute;left:620px;top:40px}
.foot-menu ul{list-style:none;margin-top:12px;font-size:10.5px;line-height:17.5px;color:var(--muted)}
.foot-brand{position:absolute;left:880px;top:84px;display:flex;align-items:center;gap:10px;color:var(--teal);font-weight:700;font-size:17px}
.foot-brand i{width:30px;height:30px;border-radius:50%;background:var(--teal)}
.follow{position:absolute;left:870px;top:150px;width:200px;text-align:center}
.follow h4{font-size:10px}
.social{display:flex;gap:8px;justify-content:center;margin-top:14px}
.social i{width:28px;height:28px;border-radius:50%;background:#1d6aa8}
.address{position:absolute;left:130px;top:258px;width:940px;border-top:1px solid var(--line);text-align:center;padding-top:14px;font-size:10px;color:var(--muted)}
.legal{position:absolute;left:130px;top:322px;width:940px;display:flex;justify-content:space-between;font-size:10px;color:var(--muted)}
</style>
</head>
<body>

<header class="site-header">
  <div class="brand"><span class="brand-dot"></span>Kelvale Heel Care</div>
  <div class="call">
    <span class="call-icon">
      <svg width="16" height="16" viewBox="0 0 24 24"><path fill="#fff" d="M6.6 10.8a15 15 0 0 0 6.6 6.6l2.2-2.2c.3-.3.7-.4 1-.2 1.1.4 2.3.6 3.6.6.6 0 1 .4 1 1V20c0 .6-.4 1-1 1A17 17 0 0 1 3 4c0-.6.4-1 1-1h3.5c.6 0 1 .4 1 1 0 1.3.2 2.5.6 3.6.1.3 0 .7-.2 1z"/></svg>
    </span>
    <div><small>CALL US NOW ON</small><strong>(08) 9472 5186</strong></div>
  </div>
  <div class="search">
    <svg width="10" height="10" viewBox="0 0 24 24"><circle cx="10" cy="10" r="7" fill="none" stroke="#888" stroke-width="3"/><path d="M15 15l7 7" stroke="#888" stroke-width="3"/></svg>SEARCH
  </div>
  <a class="btn header-book" href="#">Book Now</a>
  <nav class="main-nav">
    <a class="active" href="#">Home</a><a href="#">Common Problems</a><a href="#">Services</a><a href="#">About Us</a><a href="#">Case Histories</a><a href="#">Helpful Information</a><a href="#">Blog</a><a href="#">Contact</a>
  </nav>
</header>

<section>
  <div class="hero-photo" role="img" aria-label="Manicured hands and feet resting on a bamboo mat with a pink daisy"></div>
  <h1 class="hero-tag">We offer solutions to common foot problems</h1>
  <a class="btn" href="#" style="left:676px;top:436px;width:176px;height:49px;font-size:15px">Book Now</a>
  <div class="hero-dots"><i></i><i></i><i></i><i></i><i></i></div>
</section>

<h2 class="section-title" style="top:718px">Practice Areas</h2>

<div class="area" style="left:100px">
  <div class="area-photo" role="img" aria-label="Bare feet on a blue towel" style="background:linear-gradient(160deg,#3fb3d2,#1c8fb3)"></div>
  <h3>Common Problems</h3>
  <ul><li>Achilles Tendon Injuries</li><li>Ankle Sprains</li><li>Bunions</li></ul>
  <a class="btn" href="#">Read More</a>
</div>
<div class="area" style="left:357px">
  <div class="area-photo" role="img" aria-label="Hands massaging a foot" style="background:linear-gradient(160deg,#f4e3d6,#dcb497)"></div>
  <h3>Foot &amp; Ankle Surgery</h3>
  <ul><li>Bunion Surgery</li><li>Hammer Toes and Mallet Toes</li><li>Ingrown Toenail Surgery</li></ul>
  <a class="btn" href="#">Read More</a>
</div>
<div class="area" style="left:612px">
  <div class="area-photo" role="img" aria-label="Ballet dancers' legs en pointe" style="background:linear-gradient(160deg,#eae4dd,#c9b5a3)"></div>
  <h3>Sport and Dance</h3>
  <ul><li>Ballet Shoes &amp; Pointe Shoes</li><li>Laser Therapy for Sports Injuries</li><li>Sports Rehabilitation</li></ul>
  <a class="btn" href="#">Read More</a>
</div>
<div class="area" style="left:867px">
  <div class="area-photo" role="img" aria-label="Runner's shoes on a track" style="background:linear-gradient(160deg,#8aa0c0,#3f4c72)"></div>
  <h3>All Our Services</h3>
  <ul><li>Body Tech Treadmill</li><li>Orthotics</li><li>Children's Foot Health</li></ul>
  <a class="btn" href="#">Read More</a>
</div>

<section class="banner" role="img" aria-label="Feet with red painted toenails and a sun drawn in sunscreen on the sole, beach background">
  <h2>Let our Marrowfield podiatrists relieve your foot and ankle pain</h2>
  <p>Whether you are an office worker, pensioner, or professional athlete, nearly all people will experience problems in their feet and ankles at some point in their lives. Unfortunately, a problem in the foot can affect the whole body, causing an infection to spread, deformities in the foot, and pain to travel upward into the leg.</p>
  <a class="btn" href="#">Read More</a>
</section>

<section class="team">
  <h2 class="section-title" style="top:58px">Meet Our Team</h2>
  <span class="arrow" style="left:100px"><svg width="12" height="12" viewBox="0 0 12 12"><path d="M8 1L3 6l5 5" fill="none" stroke="#fff" stroke-width="2"/></svg></span>
  <span class="arrow" style="left:1066px"><svg width="12" height="12" viewBox="0 0 12 12"><path d="M4 1l5 5-5 5" fill="none" stroke="#fff" stroke-width="2"/></svg></span>
  <div class="member" style="left:136px"><div class="avatar" role="img" aria-label="Portrait of Rhea Calder"></div><strong>Rhea Calder</strong><span>Podiatric Surgeon</span></div>
  <div class="member" style="left:325px"><div class="avatar" role="img" aria-label="Portrait of Owen Brackett"></div><strong>Owen Brackett</strong><span>Podiatrist</span></div>
  <div class="member" style="left:515px"><div class="avatar" role="img" aria-label="Portrait of Ilsa Pemberton"></div><strong>Ilsa Pemberton</strong><span>Podiatrist</span></div>
  <div class="member" style="left:705px"><div class="avatar" role="img" aria-label="Portrait of Nora Whitcombe"></div><strong>Nora Whitcombe</strong><span>Podiatrist</span></div>
  <div class="member" style="left:900px"><div class="avatar" role="img" aria-label="Portrait of Jess Harlowe"></div><strong>Jess Harlowe</strong><span>Podiatrist</span></div>
</section>

<h2 class="section-title" style="top:2236px">Case Histories</h2>
<div class="case" role="img" aria-label="Feet photo under teal overlay" style="left:0;width:385px;background:linear-gradient(160deg,#4b9b98,#2f7f7d)"><h3>Plantar Fascia Case</h3><span>Learn More</span></div>
<div class="case" role="img" aria-label="Bunion feet photo under grey overlay" style="left:406px;width:387px;background:linear-gradient(160deg,#8a9299,#5f676e)"><h3>Bunion Case</h3><span>Learn More</span></div>
<div class="case" role="img" aria-label="Trauma treatment photo under green overlay" style="left:818px;width:382px;background:linear-gradient(160deg,#7fb07c,#4f8c55)"><h3>Trauma Case</h3><span>Learn More</span></div>
<a class="btn" href="#" style="left:495px;top:2655px;width:214px;height:36px;font-size:12px">View All Case Histories</a>

<section class="book-band" role="img" aria-label="Faded surgical theatre background"></section>
<div class="book">
  <div class="book-top"><h4>Podiatric Surgery</h4><p>Dr Rhea Calder MSc, BSc, PGradDip, FACPS</p></div>
  <div class="book-meta">Kelvale Heel Care<br>42 Tallis Road, Marrowfield WA<br>(08) 9472 5186</div>
  <div class="book-photo" role="img" aria-label="Surgeons operating in theatre"></div>
</div>
<div class="book-copy">
  <h2>Free Foot Surgery Book by<br>Podiatric Surgeon, Dr Rhea Calder</h2>
  <p>This book was created to demonstrate examples of some foot conditions that can be surgically corrected by our Podiatric Surgeon, Dr Rhea Calder.</p>
  <a class="btn" href="#">View Details</a>
</div>

<section class="affiliates" aria-label="Trusted affiliates">
  <i></i><i></i><i></i><i></i><i></i><i></i>
</section>

<footer class="site-footer">
  <h4 class="abs" style="left:130px;top:40px">Contact Us</h4>
  <div class="field" style="left:130px;top:66px;width:185px">Name</div>
  <div class="field" style="left:322px;top:66px;width:182px">E-mail</div>
  <div class="field" style="left:130px;top:108px;width:374px;height:74px">Message</div>
  <a class="btn" href="#" style="left:130px;top:198px;width:88px;height:34px;font-size:12px">Submit</a>
  <div class="foot-menu"><h4>Menu</h4>
    <ul><li>Home</li><li>Common Problems</li><li>Services</li><li>About Us</li><li>Case Histories</li><li>Helpful Information</li><li>Blog</li></ul>
  </div>
  <div class="foot-brand"><i></i>Kelvale Heel Care</div>
  <div class="follow"><h4>Follow Us</h4><div class="social"><i></i><i></i><i></i><i></i><i></i></div></div>
  <div class="address">42 Tallis Road &nbsp;|&nbsp; Marrowfield, WA 6154 &nbsp;|&nbsp; Phone: (08) 9472 5186</div>
  <div class="legal"><span>Site Map &nbsp;|&nbsp; DSS Login &nbsp;|&nbsp; Privacy Policy</span><span>Copyrights © 2017 All Rights Reserved</span></div>
</footer>

</body>
</html>
```